Seasonal Produce Calender Design

Design a seasonal fruit and vegetable calender made ready to print in various sizes. fruits and vegetables to be categorised into moths they are in season. File provided with content. Design is to flow with current company Logo, colours and brand identity. Can provide designers with link to similar calenders.

Please see link this is what im after:

https://www.brelvinharte.com.au/wp-content/uploads/2018/07/Seasonal-Calendar-Alts.jpg

Font styles to use
Serif

Colors

Designer to choose colors to be used in the design.

```html
<!DOCTYPE html>
<html lang="en">
<head>
<meta charset="utf-8">
<title>Seasonal Vegetable &amp; Fruit Calendar · Harvest Row</title>
<link rel="stylesheet" href="https://fonts.googleapis.com/css2?family=Anton&family=Oswald:wght@500;600&family=Open+Sans:wght@400;700&family=Roboto+Mono:wght@700&display=swap">
<style>
:root{
  --ink:#222;
  --black:#111;
  --white:#fff;
  --mint:#dcebdf;
  --cream:#fdf5d6;
  --summer:#e11f30;
  --autumn:#f3e21c;
  --winter:#26378c;
  --spring:#16984a;
  --label-yellow:#f5e227;
}
*{box-sizing:border-box;margin:0;padding:0}
html,body{width:1200px;height:4909px;overflow:hidden;background:var(--white)}
.canvas{position:relative;width:1200px;height:4909px;overflow:hidden;font-family:"Open Sans",Arial,sans-serif;color:var(--ink)}
.abs{position:absolute}

/* header */
.hero-photo{left:0;top:0;width:1200px;height:800px;background:linear-gradient(160deg,#5f7d45 0%,#7a3d68 28%,#a9b98a 50%,#3f5a2e 72%,#8c8e6e 100%)}
.brand-plate{left:358px;top:177px;width:476px;height:476px;border-radius:50%;background:var(--white);display:flex;align-items:center;justify-content:center}
.brand-name{font-family:"Oswald",Arial,sans-serif;font-weight:600;font-size:54px;letter-spacing:6px;color:var(--black);text-align:center;line-height:1.1}
.title-band{left:0;top:790px;width:1200px;height:108px;background:var(--black)}
.title-tail{left:1140px;top:890px;width:60px;height:130px;background:var(--black)}
.title{left:56px;top:798px;width:1090px;font-family:"Oswald",Arial,sans-serif;font-weight:600;font-size:64px;line-height:92px;color:var(--white);letter-spacing:0.5px;white-space:nowrap}

/* season words */
.season{position:absolute;overflow:visible}
.season .word{position:absolute;left:50%;top:50%;font-family:"Anton",Impact,sans-serif;line-height:1;white-space:nowrap;text-align:center}
.season.up .word{transform:translate(-50%,-50%) rotate(-90deg)}
.season.down .word{transform:translate(-50%,-50%) rotate(90deg)}
.month{position:absolute;display:flex;align-items:center;justify-content:center}
.month span{font-family:"Open Sans",Arial,sans-serif;font-weight:700;font-size:22px;letter-spacing:1.5px;white-space:nowrap}
.month.up span{transform:rotate(-90deg)}
.month.down span{transform:rotate(90deg)}
.m-black{background:var(--black)} .m-black span{color:var(--white)}
.m-yellow{background:var(--label-yellow)}

/* produce boxes */
.box{position:absolute}
.mint{background:var(--mint)}
.cream{background:var(--cream)}
.cat{position:absolute;writing-mode:vertical-rl;transform:rotate(180deg);font-family:"Open Sans",Arial,sans-serif;font-weight:700;font-size:23px;letter-spacing:4px;color:var(--black);white-space:nowrap}
.list{position:absolute;list-style:none;font-size:15.5px;line-height:25.6px;color:#333;white-space:nowrap}
.list.tight{font-size:14.5px;line-height:22px}
.list.roomy{font-size:15.5px;line-height:26.6px}
.list.big{font-size:19px;line-height:33px}

/* photos */
.photo{position:absolute;border-radius:40%}
.footer-url{left:104px;top:4812px;font-family:"Roboto Mono",monospace;font-weight:700;font-size:45px;letter-spacing:9px;color:var(--black)}
</style>
</head>
<body>
<main class="canvas">

  <header>
    <div class="abs hero-photo" role="img" aria-label="Close-up photo of fresh vegetables: cabbage, lettuce, zucchini and onions"></div>
    <div class="abs brand-plate"><div class="brand-name">HARVEST<br>ROW</div></div>
    <div class="abs title-band"></div>
    <div class="abs title-tail"></div>
    <h1 class="abs title">SEASONAL VEGETABLE &amp; FRUIT CALENDAR</h1>
  </header>

  <!-- Summer -->
  <section class="summer">
    <div class="season up" style="left:86px;top:918px;width:219px;height:827px"><div class="word" style="font-size:286px;color:var(--summer);letter-spacing:2px">SUMMER</div></div>
    <div class="month up m-black" style="left:168px;top:943px;width:40px;height:162px"><span>DECEMBER</span></div>
    <div class="month up m-black" style="left:168px;top:1234px;width:40px;height:166px"><span>JANUARY</span></div>
    <div class="month up m-black" style="left:168px;top:1572px;width:40px;height:166px"><span>FEBUARY</span></div>

    <div class="box mint" style="left:358px;top:939px;width:234px;height:810px">
      <div class="cat" style="left:22px;top:26px">FRUITS</div>
      <ul class="list" style="left:68px;top:22px">
        <li>Apricot</li><li>Banana</li><li>Blackberries</li><li>Blueberries</li><li>Boysenberries</li><li>Cantaloupe</li><li>Cherries</li><li>Currants</li><li>Fig</li><li>Grapefruit</li><li>Grapes</li><li>Honeydew</li><li>Lemon</li><li>Loganberries</li><li>Lychee</li><li>Mango</li><li>Mulberries</li><li>Nectarine</li><li>Orange Valencia</li><li>Passionfruit</li><li>Peach</li><li>Plum</li><li>Pineapple</li><li>Rambutan</li><li>Raspberries</li><li>Rhubarb</li><li>Strawberries</li><li>Tamarillo</li><li>Watermelon</li>
      </ul>
    </div>
    <div class="box cream" style="left:613px;top:939px;width:234px;height:757px">
      <div class="cat" style="left:20px;top:26px">VEGETABLES</div>
      <ul class="list" style="left:68px;top:18px;line-height:24.6px">
        <li>Asparagus</li><li>Avocado</li><li>Beans</li><li>(Butter, Green)</li><li>Beetroot</li><li>Cabbage</li><li>Capsicum</li><li>Carrot</li><li>Celery</li><li>Corn</li><li>Cucumber</li><li>Daikon</li><li>Eggplant</li><li>Leek</li><li>Lettuce</li><li>Okra</li><li>Onion</li><li>Onion, Spring</li><li>Peas</li><li>Potato</li><li>Radish</li><li>Shallot</li><li>Silverbeet</li><li>Snow Peas</li><li>Squash</li><li>Sugarsnaps</li><li>Tomato</li><li>Watercress</li><li>Zucchini</li><li>Zucchini Flower</li>
      </ul>
    </div>
    <div class="box mint" style="left:871px;top:939px;width:234px;height:515px">
      <div class="cat" style="left:20px;top:26px">HERBS &amp; SPICES</div>
      <ul class="list" style="left:68px;top:18px">
        <li>Basil</li><li>Chervil</li><li>Chilli</li><li>Chives</li><li>Coriander</li><li>Dill</li><li>Garlic</li><li>Ginger</li><li>Lime, Kaffir</li><li>(Leaves)</li><li>Lemongrass</li><li>Mint</li><li>Oregano</li><li>Parsley</li><li>Rosemary</li><li>Sage</li><li>Tarragon</li><li>Thyme</li>
      </ul>
    </div>

    <div class="photo" style="left:67px;top:1781px;width:295px;height:200px;background:radial-gradient(ellipse at 50% 55%,#e6c277 0%,#d2a652 60%,rgba(255,255,255,0) 75%)" role="img" aria-label="Photo of a pile of potatoes"></div>
    <div class="photo" style="left:676px;top:1676px;width:495px;height:290px;background:radial-gradient(ellipse at 50% 55%,#8fc14a 0%,#5f9a2c 55%,rgba(255,255,255,0) 72%)" role="img" aria-label="Photo of a head of green lettuce"></div>
  </section>

  <!-- Autumn -->
  <section class="autumn">
    <div class="box mint" style="left:86px;top:1991px;width:248px;height:772px">
      <div class="cat" style="left:18px;top:24px">FRUITS</div>
      <ul class="list tight" style="left:66px;top:12px">
        <li>Avocado</li><li>Blackberries</li><li>Banana</li><li>Cumquat</li><li>Custard Apple</li><li>Fig</li><li>Grapefruit</li><li>Grapes</li><li>Guava</li><li>Honeydew</li><li>Kiwi Fruit</li><li>Lemon</li><li>Lime</li><li>Mandarin Imperial</li><li>Mango</li><li>Mangosteen</li><li>Nashi</li><li>Orange</li><li>(Navel, Valencia)</li><li>Papaya</li><li>Passionfruit</li><li>Peach</li><li>Pear Nashi</li><li>Persimmon</li><li>Plum</li><li>Pomegranate</li><li>Prickly Pear</li><li>Quince</li><li>Rambutan</li><li>Raspberries</li><li>Rhubarb</li><li>Rockmelon</li><li>Strawberries</li><li>Tamarillo</li>
      </ul>
    </div>
    <div class="box cream" style="left:352px;top:1991px;width:467px;height:333px"></div>
    <div class="box cream" style="left:352px;top:2320px;width:229px;height:443px"></div>
    <div class="cat" style="left:368px;top:2018px">VEGETABLES</div>
    <ul class="list tight" style="left:412px;top:2016px;line-height:21.9px">
      <li>Artichoke Jerusalem</li><li>Asian Greens</li><li>(Bok Choy, Choysum,</li><li>Gailaan, Wombok)</li><li>Avocado</li><li>Beans</li><li>(Borlotti, Butter, Green)</li><li>Beetroot</li><li>Bokchoy</li><li>Broccoli</li><li>Brussels Sprouts</li><li>Cabbage</li><li>Capsicum</li><li>Carrot</li><li>Cauliflower</li><li>Celery</li><li>Choko</li><li>Corn</li><li>Cucumber</li><li>Daikon</li><li>Eggplant</li><li>Fennel</li><li>Leek</li><li>Lettuce</li><li>Mushroom</li><li>(Field, Pine,</li><li>Slippery Jacks)</li><li>Okra</li><li>Onion</li><li>Onion Spring</li><li>Parsnip</li><li>Peas</li><li>Potato</li>
    </ul>
    <ul class="list tight" style="left:648px;top:2022px;line-height:21.9px">
      <li>Pumpkin</li><li>Radish</li><li>Shallot</li><li>Silverbeet</li><li>Spinach</li><li>Squash</li><li>Swede</li><li>Sweet Potato</li><li>Tomato</li><li>Turnip</li><li>Watercress</li><li>Witlof</li><li>Zucchini</li>
    </ul>
    <div class="box mint" style="left:600px;top:2346px;width:219px;height:417px">
      <div class="cat" style="left:14px;top:20px">HERBS &amp; SPICES</div>
      <ul class="list tight" style="left:50px;top:18px">
        <li>Basil</li><li>Chervil</li><li>Chilli</li><li>Chives</li><li>Coriander</li><li>Dill</li><li>Ginger</li><li>Lime, Kaffir (Leaves)</li><li>Lemongrass</li><li>Mint</li><li>Oregano</li><li>Parsley</li><li>Rosemary</li><li>Sage</li><li>Tarragon</li><li>Thyme</li>
      </ul>
    </div>

    <div class="season down" style="left:880px;top:1991px;width:225px;height:772px"><div class="word" style="font-size:292px;color:var(--autumn)">AUTUMN</div></div>
    <div class="month down m-black" style="left:977px;top:2019px;width:42px;height:171px"><span>MARCH</span></div>
    <div class="month down m-black" style="left:977px;top:2305px;width:42px;height:171px"><span>APRIL</span></div>
    <div class="month down m-black" style="left:977px;top:2581px;width:42px;height:171px"><span>MAY</span></div>

    <div class="photo" style="left:70px;top:2795px;width:370px;height:150px;background:radial-gradient(ellipse at 50% 50%,#e8352a 0%,#c8201a 55%,rgba(255,255,255,0) 72%)" role="img" aria-label="Photo of ripe red tomatoes"></div>
    <div class="photo" style="left:490px;top:2800px;width:280px;height:170px;background:radial-gradient(ellipse at 50% 50%,#f58a1f 0%,#ea6d10 55%,rgba(255,255,255,0) 72%)" role="img" aria-label="Photo of mandarins with leaves"></div>
    <div class="photo" style="left:860px;top:2790px;width:260px;height:170px;background:radial-gradient(ellipse at 50% 50%,#d9a25a 0%,#b9782f 55%,rgba(255,255,255,0) 72%)" role="img" aria-label="Photo of brown onions"></div>
  </section>

  <!-- Winter -->
  <section class="winter">
    <div class="season up" style="left:105px;top:2990px;width:210px;height:696px"><div class="word" style="font-size:272px;color:var(--winter)">WINTER</div></div>
    <div class="month up m-yellow" style="left:185px;top:3000px;width:48px;height:162px"><span style="color:var(--winter)">JUNE</span></div>
    <div class="month up m-yellow" style="left:185px;top:3238px;width:48px;height:166px"><span style="color:var(--winter)">JULY</span></div>
    <div class="month up m-yellow" style="left:185px;top:3505px;width:48px;height:166px"><span style="color:var(--winter)">AUGUST</span></div>

    <div class="box mint" style="left:390px;top:2996px;width:223px;height:680px">
      <div class="cat" style="left:12px;top:26px">FRUITS</div>
      <ul class="list roomy" style="left:34px;top:28px">
        <li>Avocado</li><li>Cumquat</li><li>Custard Apple</li><li>Feijoa</li><li>Grapefruit</li><li>Kiwi Fruit</li><li>Lemon</li><li>Lime</li><li>Mandarin</li><li>(Ellendale, Imperial,</li><li>Murcot)</li><li>Orange</li><li>(Blood, Navel, Seville)</li><li>Pear Nashi</li><li>Persimmon</li><li>Pineapple</li><li>Quince</li><li>Rhubarb</li><li>Tamarillo</li><li>Tangelo</li>
      </ul>
    </div>
    <div class="box cream" style="left:634px;top:2996px;width:475px;height:680px">
      <div class="cat" style="left:12px;top:26px">VEGETABLES</div>
      <ul class="list roomy" style="left:67px;top:28px">
        <li>Asian Greens</li><li>( Bok Choy, Choy Sum,</li><li>Gai Laan, Wombok)</li><li>Beetroot</li><li>Broccoli</li><li>Broccolini</li><li>Beans, Broad</li><li>Brussels Sprouts</li><li>Cabbage</li><li>Carrot</li><li>Cauliflower</li><li>Celeriac</li><li>Celery</li><li>Chokos</li><li>Fennel</li><li>Horseradish</li><li>Kale</li><li>Kohlrabi</li><li>Leek</li><li>Lettuce</li><li>Mushrooms</li><li>Okra</li><li>Onion</li>
      </ul>
      <ul class="list roomy" style="left:288px;top:28px">
        <li>Onion, Spring</li><li>Parsnip</li><li>Peas</li><li>Peas, Snow</li><li>Potato</li><li>Pumpkin</li><li>Radish</li><li>Shallot</li><li>Silverbeet</li><li>Spinach</li><li>Swede</li><li>Sweet Potato</li><li>Turnip</li>
      </ul>
    </div>
    <div class="box mint" style="left:892px;top:3429px;width:217px;height:247px">
      <div class="cat" style="left:14px;top:20px">HERBS &amp; SPICES</div>
      <ul class="list big" style="left:66px;top:12px">
        <li>Ginger</li><li>Coriander</li><li>Dill</li><li>Mint</li><li>Oregano</li><li>Parsley</li><li>Rosemary</li>
      </ul>
    </div>

    <div class="photo" style="left:57px;top:3505px;width:353px;height:390px;background:radial-gradient(ellipse at 55% 45%,#6f9a3a 0%,#4c7a26 55%,rgba(255,255,255,0) 72%)" role="img" aria-label="Photo of a head of broccoli"></div>
    <div class="photo" style="left:790px;top:3715px;width:355px;height:210px;background:radial-gradient(ellipse at 50% 60%,#7a1f3a 0%,#5a1228 50%,rgba(255,255,255,0) 72%)" role="img" aria-label="Photo of beetroot with leaves"></div>
  </section>

  <!-- Spring -->
  <section class="spring">
    <div class="box mint" style="left:105px;top:3924px;width:223px;height:886px">
      <div class="cat" style="left:16px;top:40px">FRUITS</div>
      <ul class="list tight" style="left:54px;top:30px;line-height:25.6px">
        <li>Asparagus</li><li>Avocado</li><li>Banana</li><li>Blueberries</li><li>(Start Of Nov.)</li><li>Cantaloupe</li><li>Cherry</li><li>Cumquat</li><li>Grapefruit</li><li>Honeydew</li><li>Kiwi Fruit</li><li>Lemon</li><li>Lime</li><li>Loquat</li><li>Lychee</li><li>Mandarin</li><li>(Ellendale, Imperial</li><li>Murcot)</li><li>Mango</li><li>Mulberries</li><li>Orange</li><li>(Blood, Seville,</li><li>Valencia)</li><li>Papaya</li><li>Pear Corella</li><li>Pepino</li><li>Pineapple</li><li>Rhubarb</li><li>Strawberries</li><li>Starfruit</li><li>Tangelo</li><li>Watermelon</li>
      </ul>
    </div>
    <div class="box cream" style="left:352px;top:3924px;width:471px;height:352px"></div>
    <div class="box cream" style="left:352px;top:4270px;width:238px;height:540px"></div>
    <div class="cat" style="left:376px;top:3956px">VEGETABLES</div>
    <ul class="list tight" style="left:428px;top:3944px;line-height:25.8px">
      <li>Artichoke</li><li>(Globe, Jerusalem)</li><li>Asian Greens</li><li>(Bok Choy, Choy Sum,</li><li>Gai Laan, Wombok)</li><li>Beans</li><li>(Broad, Green)</li><li>Beetroot</li><li>Broccoli</li><li>Brussels Sprouts</li><li>Cabbage</li><li>Capsicum</li><li>Carrot</li><li>Cauliflower</li><li>Celery</li><li>Choko</li><li>Corn</li><li>Cucumber</li><li>Daikon</li><li>Eggplant</li><li>Fennel</li><li>Leek</li><li>Lettuce</li><li>Mushrooms</li><li>Okra</li><li>Onion</li><li>Onion, Spring</li><li>Parsnip</li><li>Peas</li><li>Potato</li><li>Pumpkin</li><li>Radish</li>
    </ul>
    <ul class="list tight" style="left:640px;top:3944px;line-height:25.8px">
      <li>Shallot</li><li>Silverbeet</li><li>Spinach</li><li>Squash</li><li>Swede</li><li>Sweet Potato</li><li>Tomato</li><li>Turnip</li><li>Watercress</li><li>Witlof</li><li>Zucchini</li>
    </ul>
    <div class="box mint" style="left:610px;top:4286px;width:213px;height:524px">
      <div class="cat" style="left:24px;top:30px">HERBS &amp; SPICES</div>
      <ul class="list tight" style="left:74px;top:20px;line-height:25.6px">
        <li>Basil</li><li>Chervil</li><li>Chilli</li><li>Chives</li><li>Coriander</li><li>Dill</li><li>Garlic</li><li>Ginger</li><li>Lime, Kaffir</li><li>(Leaves)</li><li>Lemongrass</li><li>Mint</li><li>Oregano</li><li>Parsley</li><li>Rosemary</li><li>Sage</li><li>Tarragon</li><li>Thyme</li>
      </ul>
    </div>

    <div class="season down" style="left:880px;top:3934px;width:225px;height:866px"><div class="word" style="font-size:292px;color:var(--spring);letter-spacing:8px">SPRING</div></div>
    <div class="month down m-yellow" style="left:981px;top:3972px;width:36px;height:162px"><span style="color:var(--black)">SEPTEMBER</span></div>
    <div class="month down m-yellow" style="left:981px;top:4267px;width:36px;height:162px"><span style="color:var(--black)">OCTOBER</span></div>
    <div class="month down m-yellow" style="left:981px;top:4562px;width:36px;height:162px"><span style="color:var(--black)">NOVEMBER</span></div>

    <div class="photo" style="left:830px;top:4150px;width:150px;height:100px;background:radial-gradient(ellipse at 50% 50%,#d8281c 0%,#b5160f 45%,rgba(255,255,255,0) 70%)" role="img" aria-label="Photo of a red chilli"></div>
    <div class="photo" style="left:720px;top:4625px;width:230px;height:195px;background:radial-gradient(ellipse at 50% 65%,#c8101e 0%,#9a0a15 45%,rgba(255,255,255,0) 70%)" role="img" aria-label="Photo of a pair of red cherries"></div>
  </section>

  <footer>
    <div class="abs footer-url">WWW.WEBSITE.COM</div>
  </footer>

</main>
</body>
</html>
```